Seed Oil Safety Card for Healthy Restaurant Dining

I am seeking a design for a physical card to communicate my wife's health-related dietary restriction regarding seed oils. This card will be given to restaurant waiters to ensure her meals are prepared without seed oils, as it is a health issue and not merely a preference.
My wife cannot eat any “seed oil” or “processed oil”, including:
- Vegetable oil
- Canola oil
- Soybean oil
- Sunflower oil
- Corn oil
- Cottonseed oil
- Safflower oil
- Peanut oil
- Sesame oil
Oils that are OK for her to consume:
- Butter (most preferable)
- Extra virgin olive oil
- Avocado oil
- Coconut oil
- Ghee
- Lard
- Any other animal-based fats
Key Design Requirements:
- Clarity and speed of communication: The card should be easily read and understood by waiters, even in low-light environments, emphasizing that it's a health concern.
- Avoid common misconceptions: Ensure the design doesn't imply common dietary preferences like "vegetarian" or "no butter." Animal fats and butter are actually preferable for her!
- Preferred term: Use "seed oils" as the term to describe what she cannot eat due to her health issue.
- Trace amounts are acceptable: Communicate that it's OK to use cookware that has previously been in contact with seed oils, but not to have seed oil as an ingredient. Please suggest a concise way to convey this.
- Card dimensions: Design should be 3.5” x 2.25” (standard credit-card size on printorvale.example). Horizontal or vertical layouts are both fine, whichever makes the message clearer.
Design Suggestions:
- Utilize bold and easy-to-read typography to communicate the main message.
- Consider incorporating relevant icons or graphics that help convey the message without adding confusion.
- Use contrasting colors to enhance readability, especially in low-light situations.
- To communicate the “trace amounts OK” part, consider phrases such as:
- "Cross-contamination acceptable"
- “Used cookware OK, no ingredient use”
- “Separate cookware not necessary”
Thank you for your assistance in creating this essential card for my wife's health and safety when dining out!

```html
<!DOCTYPE html>
<html lang="en">
<head>
<meta charset="utf-8">
<title>Seed Oil Safety Card</title>
<link href="https://fonts.googleapis.com/css2?family=Roboto+Condensed:ital,wght@0,400;0,700;1,400&display=swap" rel="stylesheet">
<style>
  :root {
    --page-bg: #a3a3a3;
    --card-bg: #ffffff;
    --ink: #0f2a36;
    --avoid: #c8161d;
    --allow: #1f9a35;
  }
  * { box-sizing: border-box; margin: 0; padding: 0; }
  html, body {
    width: 1200px; height: 1200px; overflow: hidden;
    background: var(--page-bg);
    font-family: "Roboto Condensed", "Arial Narrow", sans-serif;
  }
  .card {
    position: absolute; left: 246px; top: 50px;
    width: 707px; height: 1100px;
    background: var(--card-bg);
    border-radius: 65px;
  }
  .card-title {
    position: absolute; left: 0; top: 55px; width: 100%;
    text-align: center; color: var(--ink);
    font-weight: 700; font-size: 43px; line-height: 46px;
    letter-spacing: 1px;
  }
  .title-rule {
    position: absolute; left: 189px; top: 155px;
    width: 329px; height: 6px; background: var(--ink);
  }
  .column-badge { position: absolute; top: 206px; width: 86px; height: 86px; }
  .badge-avoid { left: 150px; }
  .badge-allow { left: 467px; }
  .column-heading {
    position: absolute; top: 302px; width: 280px;
    text-align: center; color: var(--ink);
    font-weight: 700; font-size: 31px; line-height: 31px; letter-spacing: 1px;
  }
  .heading-avoid { left: 53px; }
  .heading-allow { left: 370px; top: 300px; }
  .pointer { position: absolute; top: 441px; width: 46px; height: 25px; }
  .pointer-avoid { left: 170px; }
  .pointer-allow { left: 487px; }
  .oil-list {
    position: absolute; top: 489px; list-style: none;
    font-size: 31px; line-height: 43.6px; letter-spacing: 0.5px;
  }
  .list-avoid { left: 80px; color: var(--avoid); }
  .list-allow { left: 373px; color: var(--allow); }
  .oil-list li { position: relative; padding-left: 33px; }
  .oil-list li.continued { padding-left: 33px; }
  .oil-list li svg {
    position: absolute; left: 0; top: 12px; width: 20px; height: 20px;
  }
  .cookware-note {
    position: absolute; left: 0; top: 953px; width: 100%;
    text-align: center; color: var(--ink);
    font-style: italic; font-size: 29px; line-height: 35px; letter-spacing: 0.5px;
  }
</style>
</head>
<body>
<main class="card">
  <h1 class="card-title">MY WIFE'S HEALTH AND SAFETY<br>WHEN DINING OUT!</h1>
  <div class="title-rule"></div>

  <svg class="column-badge badge-avoid" viewBox="0 0 86 86" aria-hidden="true">
    <rect x="2.5" y="2.5" width="81" height="81" rx="3" fill="none" stroke="var(--avoid)" stroke-width="5"/>
    <path d="M22 22 L64 64 M64 22 L22 64" stroke="var(--avoid)" stroke-width="12"/>
  </svg>
  <svg class="column-badge badge-allow" viewBox="0 0 86 86" aria-hidden="true">
    <rect x="2.5" y="2.5" width="81" height="81" rx="3" fill="none" stroke="var(--allow)" stroke-width="5"/>
    <path d="M20 44 L36 60 L66 22" fill="none" stroke="var(--allow)" stroke-width="12"/>
  </svg>

  <h2 class="column-heading heading-avoid">Cannot Eat<br>Any Seed Oil or<br>Processed Oil,<br>Including:</h2>
  <h2 class="column-heading heading-allow">Oils That<br>Are OK<br>For Her<br>To Consume:</h2>

  <svg class="pointer pointer-avoid" viewBox="0 0 46 25" aria-hidden="true"><path d="M0 0 H46 L23 25 Z" fill="var(--ink)"/></svg>
  <svg class="pointer pointer-allow" viewBox="0 0 46 25" aria-hidden="true"><path d="M0 0 H46 L23 25 Z" fill="var(--ink)"/></svg>

  <ul class="oil-list list-avoid">
    <li><svg viewBox="0 0 20 20"><rect x="1.5" y="1.5" width="17" height="17" fill="none" stroke="currentColor" stroke-width="2"/><path d="M6 6 L14 14 M14 6 L6 14" stroke="currentColor" stroke-width="2.5"/></svg>Vegetable oil</li>
    <li><svg viewBox="0 0 20 20"><rect x="1.5" y="1.5" width="17" height="17" fill="none" stroke="currentColor" stroke-width="2"/><path d="M6 6 L14 14 M14 6 L6 14" stroke="currentColor" stroke-width="2.5"/></svg>Canola oil</li>
    <li><svg viewBox="0 0 20 20"><rect x="1.5" y="1.5" width="17" height="17" fill="none" stroke="currentColor" stroke-width="2"/><path d="M6 6 L14 14 M14 6 L6 14" stroke="currentColor" stroke-width="2.5"/></svg>Soybean oil</li>
    <li><svg viewBox="0 0 20 20"><rect x="1.5" y="1.5" width="17" height="17" fill="none" stroke="currentColor" stroke-width="2"/><path d="M6 6 L14 14 M14 6 L6 14" stroke="currentColor" stroke-width="2.5"/></svg>Sunflower oil</li>
    <li><svg viewBox="0 0 20 20"><rect x="1.5" y="1.5" width="17" height="17" fill="none" stroke="currentColor" stroke-width="2"/><path d="M6 6 L14 14 M14 6 L6 14" stroke="currentColor" stroke-width="2.5"/></svg>Corn oil</li>
    <li><svg viewBox="0 0 20 20"><rect x="1.5" y="1.5" width="17" height="17" fill="none" stroke="currentColor" stroke-width="2"/><path d="M6 6 L14 14 M14 6 L6 14" stroke="currentColor" stroke-width="2.5"/></svg>Cottonseed oil</li>
    <li><svg viewBox="0 0 20 20"><rect x="1.5" y="1.5" width="17" height="17" fill="none" stroke="currentColor" stroke-width="2"/><path d="M6 6 L14 14 M14 6 L6 14" stroke="currentColor" stroke-width="2.5"/></svg>Safflower oil</li>
    <li><svg viewBox="0 0 20 20"><rect x="1.5" y="1.5" width="17" height="17" fill="none" stroke="currentColor" stroke-width="2"/><path d="M6 6 L14 14 M14 6 L6 14" stroke="currentColor" stroke-width="2.5"/></svg>Peanut oil</li>
    <li><svg viewBox="0 0 20 20"><rect x="1.5" y="1.5" width="17" height="17" fill="none" stroke="currentColor" stroke-width="2"/><path d="M6 6 L14 14 M14 6 L6 14" stroke="currentColor" stroke-width="2.5"/></svg>Sesame oil</li>
  </ul>

  <ul class="oil-list list-allow">
    <li><svg viewBox="0 0 20 20"><rect x="1.5" y="1.5" width="17" height="17" fill="none" stroke="currentColor" stroke-width="2"/><path d="M5.5 10 L9 13.5 L14.5 6.5" fill="none" stroke="currentColor" stroke-width="2.5"/></svg>Butter</li>
    <li class="continued">(most preferable)</li>
    <li><svg viewBox="0 0 20 20"><rect x="1.5" y="1.5" width="17" height="17" fill="none" stroke="currentColor" stroke-width="2"/><path d="M5.5 10 L9 13.5 L14.5 6.5" fill="none" stroke="currentColor" stroke-width="2.5"/></svg>Extra virgin</li>
    <li><svg viewBox="0 0 20 20"><rect x="1.5" y="1.5" width="17" height="17" fill="none" stroke="currentColor" stroke-width="2"/><path d="M5.5 10 L9 13.5 L14.5 6.5" fill="none" stroke="currentColor" stroke-width="2.5"/></svg>Olive oil</li>
    <li><svg viewBox="0 0 20 20"><rect x="1.5" y="1.5" width="17" height="17" fill="none" stroke="currentColor" stroke-width="2"/><path d="M5.5 10 L9 13.5 L14.5 6.5" fill="none" stroke="currentColor" stroke-width="2.5"/></svg>Avocado oil</li>
    <li><svg viewBox="0 0 20 20"><rect x="1.5" y="1.5" width="17" height="17" fill="none" stroke="currentColor" stroke-width="2"/><path d="M5.5 10 L9 13.5 L14.5 6.5" fill="none" stroke="currentColor" stroke-width="2.5"/></svg>Coconut oil</li>
    <li><svg viewBox="0 0 20 20"><rect x="1.5" y="1.5" width="17" height="17" fill="none" stroke="currentColor" stroke-width="2"/><path d="M5.5 10 L9 13.5 L14.5 6.5" fill="none" stroke="currentColor" stroke-width="2.5"/></svg>Ghee</li>
    <li><svg viewBox="0 0 20 20"><rect x="1.5" y="1.5" width="17" height="17" fill="none" stroke="currentColor" stroke-width="2"/><path d="M5.5 10 L9 13.5 L14.5 6.5" fill="none" stroke="currentColor" stroke-width="2.5"/></svg>Lard</li>
    <li><svg viewBox="0 0 20 20"><rect x="1.5" y="1.5" width="17" height="17" fill="none" stroke="currentColor" stroke-width="2"/><path d="M5.5 10 L9 13.5 L14.5 6.5" fill="none" stroke="currentColor" stroke-width="2.5"/></svg>Any other</li>
    <li class="continued">animal-based fats</li>
  </ul>

  <p class="cookware-note">"Cross-contamination acceptable"<br>“Used cookware OK, no ingredient use”<br>“Separate cookware not necessary”</p>
</main>
</body>
</html>
```